Financial Advisor Resource Firm needs business card design

Need business card design for company in Omaha NE called Meridale Circle. We provide resources to financial advisors....workshop programs, retirement analysis, and insurance planning. I would like to see designs that use grays, greens, black, and white colors. The final design should communicate 'collaboration' and be simple yet attractive to financial planning clients. I will attached our logo and another picture of a puzzle piece coming together. I would like the incorporate the puzzle picture somehow, maybe on the back somehow, with color or just the gray scale....OR, the picture be the front of the card with 'Meridale' definition on it (see upload) and then company logo, employee name, title, address on the back (see ppt uploaded). The following disclosure needs to be included somewhere- Advisory services offered through Stonebrook Assets, LLC.
Updates

I uploaded a svg and ai file of the logo

Target Market(s)

Financial planning clients and financial advisors....so pretty diverse age range of about 40-70.

Industry/Entity Type

Financial Planning

Contact Information for Business Card

Tobias L. Fenwright, MBA
Founder/President
5287 E. Larkin Road
Suite 230
Omaha, NE 68190
Phone- (402) 555-0147
Cell- (402) 555-0183
Fax- (402) 555-0129
email- tobias@meridaleplan.example
web address- www.meridaleplan.example

Colors
1b1b1b
474747
d3d3d3
ffffff
9bcb3c
abd036

Requirements
Must have
• Must include logo provided, must be 2 sided, and must have disclosure...all of these items listed in project description

```html
<!DOCTYPE html>
<html lang="en">
<head>
<meta charset="utf-8">
<title>Meridale Circle — Business Card</title>
<link rel="stylesheet" href="https://fonts.googleapis.com/css2?family=Roboto:wght@400;500&family=Work+Sans:wght@400&family=Cormorant+Garamond:wght@500&family=Source+Sans+3:wght@400;600&display=swap">
<style>
  :root {
    --page: #dedede;
    --ink: #1b1b1b;
    --black: #000000;
    --green: #8dc63f;
    --green-bright: #9bcb3c;
    --white: #ffffff;
    --gray-dark: #2e2e2e;
    --gray-mid: #474747;
    --gray-light: #8a8a8a;
  }
  * { margin: 0; padding: 0; box-sizing: border-box; }
  html, body {
    width: 1200px; height: 897px; overflow: hidden;
    background: var(--page);
  }
  .canvas { position: relative; width: 1200px; height: 897px; }

  .card {
    position: absolute; left: 329px; width: 543px; height: 310px;
    overflow: hidden;
  }

  /* Front */
  .card-front { top: 108px; background: var(--black); }
  .card-front .accent-band {
    position: absolute; left: 0; right: 0; bottom: 0; height: 8px;
    background: var(--green);
  }
  .card-front .accent-gap {
    position: absolute; left: 0; right: 0; bottom: 8px; height: 2px;
    background: var(--white);
  }
  .brand {
    position: absolute; left: 26px; top: 143px; width: 210px;
    display: flex; align-items: center; gap: 8px;
    font-family: "Work Sans", sans-serif; font-size: 21px; font-weight: 400;
    color: var(--white); white-space: nowrap; letter-spacing: 0.3px;
  }
  .brand-dot {
    width: 14px; height: 14px; border-radius: 50%;
    background: var(--green); flex: none;
  }
  .disclosure {
    position: absolute; left: 26px; top: 278px; white-space: nowrap;
    font-family: "Work Sans", sans-serif; font-size: 8.5px;
    color: var(--gray-light); line-height: 1;
  }
  .divider {
    position: absolute; left: 259px; top: 58px; width: 1.5px; height: 192px;
    background: var(--green);
  }
  .contact { position: absolute; left: 283px; top: 0; right: 0; }
  .person-name {
    position: absolute; top: 56px; white-space: nowrap;
    font-family: "Roboto", sans-serif; font-weight: 500; font-size: 21px;
    color: var(--green); letter-spacing: -0.2px;
  }
  .person-title, .address-line, .contact-line {
    position: absolute; white-space: nowrap;
    font-family: "Work Sans", sans-serif; font-size: 13.6px;
    color: var(--white); line-height: 1;
  }
  .person-title { top: 81px; }
  .address-line.first { top: 111px; }
  .address-line.second { top: 130px; }
  .contact-line { left: 18px; }
  .contact-line .icon {
    position: absolute; left: -17px; top: 2px; width: 9px; height: 9px;
  }
  .contact-line.l1 { top: 161px; }
  .contact-line.l2 { top: 180px; }
  .contact-line.l3 { top: 199px; }
  .contact-line.l4 { top: 218px; }
  .contact-line.l5 { top: 237px; }
  .web-name { color: var(--green); }

  /* Back */
  .card-back { top: 479px; background: var(--gray-dark); }
  .puzzle-photo {
    position: absolute; inset: 0;
    background:
      radial-gradient(ellipse at 30% 20%, #6a6a6a 0%, transparent 55%),
      radial-gradient(ellipse at 80% 60%, #5a5a5a 0%, transparent 50%),
      linear-gradient(160deg, #5c5c5c 0%, #3a3a3a 55%, #1f1f1f 100%);
  }
  .definition { position: absolute; inset: 0; text-align: center; }
  .term {
    position: absolute; left: 0; right: 0; top: 110px;
    font-family: "Cormorant Garamond", serif; font-weight: 500; font-size: 38px;
    color: var(--green-bright); letter-spacing: 0.5px;
  }
  .pronunciation {
    position: absolute; left: 0; right: 0; top: 152px;
    font-family: "Source Sans 3", sans-serif; font-weight: 600; font-size: 16px;
    color: var(--white);
  }
  .meaning {
    position: absolute; left: 0; right: 0; top: 188px;
    font-family: "Source Sans 3", sans-serif; font-weight: 400; font-size: 15.3px;
    color: var(--white);
  }
</style>
</head>
<body>
<div class="canvas">

  <section class="card card-front">
    <div class="brand"><span class="brand-dot"></span>Meridale Circle</div>
    <div class="divider"></div>
    <div class="contact">
      <div class="person-name">Tobias L. Fenwright, MBA</div>
      <div class="person-title">Founder/President</div>
      <div class="address-line first">5287 E. Larkin Road</div>
      <div class="address-line second">Suite 230 Omaha, NE 68190</div>

      <div class="contact-line l1">
        <svg class="icon" viewBox="0 0 10 10" aria-hidden="true"><path d="M2 0.5 L3.6 2.6 L2.8 3.6 Q4 6 6.4 7.2 L7.4 6.4 L9.5 8 L8.4 9.5 Q4 9 1 5 Q0.3 2.5 2 0.5Z" fill="var(--green)"/></svg>
        (402) 555-0147
      </div>
      <div class="contact-line l2">
        <svg class="icon" viewBox="0 0 10 10" aria-hidden="true"><rect x="2.5" y="0.5" width="5" height="9" rx="1" fill="none" stroke="var(--green)" stroke-width="1.3"/><rect x="4.3" y="7.3" width="1.4" height="1" fill="var(--green)"/></svg>
        (402) 555-0183
      </div>
      <div class="contact-line l3">
        <svg class="icon" viewBox="0 0 10 10" aria-hidden="true"><rect x="2.5" y="0.5" width="5" height="3" fill="var(--green)"/><rect x="0.5" y="3.5" width="9" height="4" rx="1" fill="var(--green)"/><rect x="2.5" y="6.5" width="5" height="3" fill="var(--green)"/></svg>
        (402) 555-0129
      </div>
      <div class="contact-line l4">
        <svg class="icon" viewBox="0 0 10 10" aria-hidden="true"><rect x="0.7" y="2" width="8.6" height="6" fill="none" stroke="var(--green)" stroke-width="1.2"/><path d="M0.7 2 L5 5.5 L9.3 2" fill="none" stroke="var(--green)" stroke-width="1.2"/></svg>
        tobias@meridaleplan.example
      </div>
      <div class="contact-line l5">
        <svg class="icon" viewBox="0 0 10 10" aria-hidden="true"><circle cx="5" cy="5" r="4.3" fill="none" stroke="var(--green)" stroke-width="1"/><ellipse cx="5" cy="5" rx="1.8" ry="4.3" fill="none" stroke="var(--green)" stroke-width="0.9"/><path d="M0.7 5 H9.3 M1.4 3 H8.6 M1.4 7 H8.6" stroke="var(--green)" stroke-width="0.8"/></svg>
        www.<span class="web-name">meridaleplan</span>.example
      </div>
    </div>
    <div class="disclosure">Advisory services offered through Stonebrook Assets, LLC.</div>
    <div class="accent-gap"></div>
    <div class="accent-band"></div>
  </section>

  <section class="card card-back">
    <div class="puzzle-photo" role="img" aria-label="Grayscale photograph of hands joining two puzzle pieces"></div>
    <div class="definition">
      <div class="term">MER·I·DALE</div>
      <div class="pronunciation">ˈmer·ə·dāl</div>
      <div class="meaning">: to come together and unite in common interest and focus</div>
    </div>
  </section>

</div>
</body>
</html>
```